SaaS / Consulting / Solution website redesign

We need a website design that:
- Is completely different than our current design : https://plumvessel.net
- Has a very minimal amount of copy
- Changes our positioning from a SaaS application to a solutions company. Solutions company means that we help our customers solve their problems with consulting, training, and tools. An example of a solutions company is here: https://oldpages.example/web/20130111103320/http://www.brindlework.com:80/
- Does not make us look like a start up
- Is more people oriented than technology oriented

We need a designer that:
- Is a rebel at heart
- Is a minimalist
- Tells us why our current site sucks
- Can disagree with us
- Can also do copywriting or already has a copywriter that can help
- Is ok with saying we have capability that we don't in order to see if people actually want that
- Can understand the difference between our grand vision and where we need to focus ourselves today in order to get there

Who we are:
- Entrepreneurs
- Programmers
- Consultants
- Investors

Here's our design goals:
#1 Get customers, investors, employers, and partners excited about our unique and clearly articulated value proposition
#2 Get people to contact us asking for help with their programs
#3 Position ourselves as an expert in the skills based volunteering, mentorship, and group collaboration
#4 Make it easy for people, who already know who we are, to register online

What our grand vision is:
- Create a marketplace where any person can go to our site and find time with anyone they need to meet with. Whether that is their hair stylist, school advisor, parent of your kids class, dentist, attorney, etc.

What will you get if you win:
- In addition to the prize of this project we will have many landing pages and other revisions we will need in the future. We currently don't have a designer or copywriter and need to add that capability to our team

Who do we need to appeal to:
- Directors that are launching innovative programs inside organizations
- IT personnel who are trying to disqualify our technology so they don't have to support it or deal with it when it doesn't go well
- Enterprise IT architects who don't want our product being on its own island within their organization totally incompatible with everything else. Architects which are trying to assess how our platform will co-exist with all their other platforms
- Vice Presidents who want to help their directors understand that we don't have enough experience to help them
- Program managers who have to juggle a million things and need a tool that actually helps instead of confuses them and adds more work for them.
- Program managers & directors that have been given ambiguous goals by their board of directors like "improve retention, increase engagement, create innovation, get people to collaborate." And who have no idea where to start or how to deliver on things like that.
- Program managers, directors, and vice presidents that are trying to understand how our technology and services fit into their existing technology and capability
- Employees who are bored and uninspired with their current tools and are hoping for some excitement in their life. Kind of like candy or a double espresso.
- Investors who think, our company like all the rest, are going to waste their money and make them look like a fool

Other information:
-The CSS and html needs to be responsive

-Our registration onboarding flow needs to collect this information:
User first name
user last name
user email
(verify their email)
user phone number
(verify their phone number)
User profile image (optional)
User profile summary (optional, like a bio, freeform text fiels)
If applicable: Register their organization
Organization name
Organization image (optional)
Account Mailing address
account Billing address (could be same as mailing address)
account Billing email address (could be same as user address)
account Product selection (pricing tier)
account Credit card information

The designs I am getting are a good start but they are only the front page. I just want you to know that I am expecting and need more than a landing page to complete the design. I will likely need a page that outlines the benefits and features of the product itself, how its different than our competitors, which will not be on the front page. I will need a registration flow. I will need a blog page design so we can post blog articles, I will need a team page, a page that goes into detail on our training, our services. I will likely need a page that shows all news and media we have been in. I need to show customer and user quotes, case studies, a way to contact us, partners, general resources like on collaboration, product tutorials, customers. I need the site to address a comprehensive set of needs. I need that design to be consistent and thorough. I know what PlateHarbor is. I'm not using because I need more than a template that was customized. I need to be unique and match our brand thoughtfully, beautifully, and artistically. Someone asked me a question about how Murmly is similar to our tool in the way it is referred by end users and purchased by managers. Our website needs to primarily talk to the managers as I explained in the brief but it needs to appear cool and exciting to our end-users without focusing on the technology too much. Murmly is a tool that teams use to collaborate in small and large enterprises. The value prop for them is that communication is easier. But they don't put that on their website. Why? Because the users of the technology won't go to the website to find out information on it, they get their information from someone who is using it and demos it to them. When Ines tells her manager Otto "Lets get murmly, Ruth is using it at her company and its great" Ines's manager doesn't know anything about murmly so she promptly googles it. The most important thing from Ines's perspective is that Otto agrees to try it out. Otto's biggest concern is that productivity will be enhanced to degraded. Murmly knows this and so on the front page they know they are talking to Otto NOT Ines because Ines is already sold on it and doesn't need to get sold on the website. Ines is end user. Otto is the purchaser. We have the same problem and so our end users are not the ones purchasing our product, their managers are purchasing our product. We get referred by our end users and vetted by their managers. Hope this helps! Thank you for looking at this project!  Added Wednesday, June 7, 2017

Another observation I am having about the designs being submitted. I believe we used the animations on our current website because animations / cartoons connect with the "inner child" in our users. Whatever that means :-). I think it's what makes our brand fun. I have a hard time imagining that we could make the design fun looking without animations but I'm sure it can be achieved. I also recognize that blending pictures of real people and animations is hard. So either we must masterfully blend them, use only animations, or make the real people have a LOT of fun! So far most of the designs while achieve the goal of appealing to the serious Vice Presidents and directors, they are not doing a good job at appealing to the overworked program managers and bored employees. There seems to stand another challenge with animations which is animations are hard to find and/or create that achieve the message / emotion we are trying to communicate. I don't have any good answers for this but I will say we can hire both animators and illustrators if we need to. All you have to do is communicate the effect in the website design with some simpler version maybe not the end illustration or animation itself. Added Wednesday, June 7, 2017

• Sex appeal and a sense of humor. Copy that makes people excited and clairvoyant about our potential.
• Boring renditions of other non-inspiring websites

```html
<!DOCTYPE html>
<html lang="en">
<head>
<meta charset="utf-8">
<title>Plumvessel – Register Now</title>
<link rel="stylesheet" href="https://fonts.googleapis.com/css2?family=Roboto:wght@300;400;500&display=swap">
<style>
  :root {
    --sky-top: #3d9de3;
    --sky-mid: #3590db;
    --sky-bottom: #2a82cc;
    --glow: rgba(255, 255, 255, 0.06);
    --deep-band: #0f5a93;
    --white: #ffffff;
    --field-text: #333333;
    --field-shadow: rgba(10, 50, 90, 0.45);
    --button-top: #efefef;
    --button-bottom: #c2c2c2;
    --button-edge: #f4f4f4;
    --button-text: #2a78c2;
  }

  * { box-sizing: border-box; margin: 0; padding: 0; }

  html, body {
    width: 1200px;
    height: 842px;
    overflow: hidden;
  }

  body {
    position: relative;
    font-family: "Roboto", Arial, sans-serif;
  }

  .backdrop {
    position: absolute;
    inset: 0;
    background:
      radial-gradient(ellipse 420px 300px at 150px 160px, var(--glow), transparent 70%),
      radial-gradient(ellipse 380px 260px at 1000px 700px, var(--glow), transparent 70%),
      radial-gradient(ellipse 320px 240px at 200px 720px, var(--glow), transparent 70%),
      linear-gradient(180deg, var(--sky-top) 0%, var(--sky-mid) 50%, var(--sky-bottom) 100%);
  }

  .footer-band {
    position: absolute;
    left: 0;
    bottom: 0;
    width: 100%;
    height: 4px;
    background: var(--deep-band);
  }

  .register-page {
    position: relative;
    width: 100%;
    height: 100%;
  }

  .brand {
    position: absolute;
    top: 66px;
    left: 0;
    width: 100%;
    display: flex;
    justify-content: center;
    align-items: center;
    gap: 12px;
  }

  .brand-dot {
    width: 58px;
    height: 58px;
    border: 6px solid var(--white);
    border-radius: 50%;
  }

  .brand-name {
    font-size: 42px;
    font-weight: 500;
    color: var(--white);
    letter-spacing: 0.5px;
  }

  .page-title {
    position: absolute;
    top: 187px;
    left: 0;
    width: 100%;
    text-align: center;
    font-size: 38px;
    line-height: 48px;
    font-weight: 400;
    color: var(--white);
    text-shadow: 1px 2px 3px rgba(0, 0, 0, 0.35);
    letter-spacing: 0.2px;
  }

  .register-form {
    position: absolute;
    top: 257px;
    left: 399px;
    width: 403px;
    display: flex;
    flex-direction: column;
    gap: 15px;
  }

  .field {
    display: block;
    width: 100%;
    height: 47px;
    border: none;
    background: var(--white);
    box-shadow: 1px 2px 3px var(--field-shadow);
    padding: 0 13px;
    font-family: "Roboto", Arial, sans-serif;
    font-size: 12.5px;
    font-weight: 400;
    color: var(--field-text);
  }

  .field::placeholder { color: var(--field-text); opacity: 1; }

  .field-summary {
    height: 100px;
    padding-top: 16px;
    resize: none;
  }

  .submit-button {
    position: absolute;
    top: 696px;
    left: 498px;
    width: 204px;
    height: 52px;
    border: 1px solid var(--button-edge);
    border-radius: 3px;
    background: linear-gradient(180deg, var(--button-top) 0%, var(--button-bottom) 100%);
    font-family: "Roboto", Arial, sans-serif;
    font-size: 18px;
    font-weight: 400;
    letter-spacing: 0.8px;
    color: var(--button-text);
    cursor: pointer;
  }
</style>
</head>
<body>
  <div class="backdrop" role="img" aria-label="Blue background with a faint pattern of connected network dots and lines"></div>

  <main class="register-page">
    <div class="brand">
      <span class="brand-dot"></span>
      <span class="brand-name">Plumvessel</span>
    </div>

    <h1 class="page-title">REGISTER NOW</h1>

    <form class="register-form">
      <input class="field" type="text" name="first-name" placeholder="First Name">
      <input class="field" type="text" name="last-name" placeholder="Last Name">
      <input class="field" type="email" name="email" placeholder="Email">
      <input class="field" type="tel" name="phone" placeholder="Phone">
      <input class="field" type="text" name="profile-image" placeholder="Profile Image (Optional)">
      <textarea class="field field-summary" name="profile-summary" placeholder="Profile Summary (Optional)"></textarea>
    </form>

    <button class="submit-button" type="button">SUBSCRIBE</button>
  </main>

  <div class="footer-band"></div>
</body>
</html>
```